I need a letterhead for a newsletter that will go out quarterly to the dentists of the 18th district. It is called "The Crestline Digest" We are in Amarillo TX and have this landmark in the photo as our most prominent feature. If it could be used, that would be cool.
This is a professional organization newsletter so the letterhead should be somewhat professional.

Target Market(s)

Dentists

Industry/Entity Type

Dental

Font styles to use
Serif

Colors

Designer to choose only greyscale colors for use in the design.

Requirements
Must have
• I want the title of "The Crestline Digest" to be the on top with the phrase "Cobalt Ridge Dental Society" written underneath.
Nice to have
• the photo incorporated could be incorporated in black and white or color along the bottom of the letterhead or with the title inside the photo.
Should not have
• I don't want it to be cartoony. I want it to be stylish and elegant and professional.

```html
<!DOCTYPE html>
<html lang="en">
<head>
<meta charset="utf-8">
<title>The Crestline Digest — Letterhead</title>
<link rel="stylesheet" href="https://fonts.googleapis.com/css2?family=Cormorant+SC:wght@500;600&family=EB+Garamond:wght@400;500&display=swap">
<style>
  :root {
    --backdrop: #e4e4e4;
    --paper: #ffffff;
    --panel-grey: #555555;
    --ink: #000000;
    --type-light: #ffffff;
    --photo-dark: #3a3a3a;
    --photo-mid: #7a7a7a;
    --photo-light: #a8a8a8;
  }
  * { box-sizing: border-box; margin: 0; padding: 0; }
  html, body {
    width: 1200px;
    height: 898px;
    overflow: hidden;
    background: var(--backdrop);
  }
  .letterhead {
    position: absolute;
    left: 270px;
    top: 22px;
    width: 660px;
    height: 854px;
    background: var(--paper);
    box-shadow: 0 6px 24px rgba(0, 0, 0, 0.15);
  }
  .cover-photo {
    position: absolute;
    left: 20px;
    top: 60px;
    width: 340px;
    height: 222px;
    border: 2px solid var(--ink);
    background: linear-gradient(100deg, var(--photo-dark) 0%, var(--photo-mid) 40%, var(--photo-light) 58%, var(--photo-mid) 72%, #8e8e8e 100%);
  }
  .title-panel {
    position: absolute;
    left: 372px;
    top: 22px;
    width: 262px;
    height: 250px;
    background: var(--panel-grey);
    color: var(--type-light);
    padding: 96px 0 0 22px;
  }
  .title-panel__name {
    font-family: "Cormorant SC", serif;
    font-weight: 600;
    font-size: 23px;
    line-height: 1;
    letter-spacing: 0.3px;
    white-space: nowrap;
  }
  .title-panel__society {
    font-family: "Cormorant SC", serif;
    font-weight: 600;
    font-size: 12.5px;
    letter-spacing: 0.4px;
    margin-top: 6px;
    white-space: nowrap;
  }
  .series-band {
    position: absolute;
    left: 380px;
    top: 278px;
    width: 264px;
    height: 22px;
    background: var(--ink);
    color: var(--type-light);
    font-family: "EB Garamond", serif;
    font-size: 15.5px;
    line-height: 22px;
    padding-left: 6px;
    letter-spacing: 0.3px;
    white-space: nowrap;
  }
  .issue-band {
    position: absolute;
    left: 64px;
    top: 284px;
    width: 306px;
    height: 24px;
    background: var(--panel-grey);
    color: var(--type-light);
    font-family: "Cormorant SC", serif;
    font-weight: 600;
    font-size: 15px;
    line-height: 24px;
    display: flex;
    justify-content: space-between;
    padding: 0 18px 0 26px;
    white-space: nowrap;
  }
</style>
</head>
<body>
  <main class="letterhead">
    <div class="cover-photo" role="img" aria-label="Black and white photograph of a sandstone canyon tower landmark"></div>
    <header class="title-panel">
      <h1 class="title-panel__name">The Crestline Digest</h1>
      <p class="title-panel__society">Cobalt Ridge Dental Society</p>
    </header>
    <div class="series-band">QUARTERLY NEWSLETTER</div>
    <div class="issue-band">
      <span class="issue-band__date">Oct 2019</span>
      <span class="issue-band__number">ISSUE NO 01</span>
    </div>
  </main>
</body>
</html>
```